2-3 Eröffnungsplakate mit Text und Bild
Zielgruppe
Wir verkaufen Industridesign Möbel , Massivholz Tische , Lederstühle und Sitzbänke sowie Loungesessel zu Fabrikpreisen. Zielgruppe ist 25-50 , Stilorientiert und Modebewusst. Individualisten die gerne Ihr Zuhause nicht von der Stange einrichten.
Aufgabenstellung
Wir eröffnen in ca 3 Wochen einen neuen Laden mit unserer Möbel. Der Laden ist direkt an einer viel befahrenen straße. Das Plakat soll für die Neueröffnung werben und eines oder mehrere der angefügten Bilder beinhalten. Die Plakate werden Bauzaungroß also
340cm x 173cm
Es darf nicht viel Text vorkommen, sodass man beim vorbeifahren alles wichtige Lesen kann. Textbeispiele :
- NEUERÖFFNUNG. Massivholztische zu Fabrikpreisen
- NEUERÖFFNUNG. WOHNEN IM LOFT UND INDUSTRIDESIGN ZU HERSTELLERPREISEN
- NEUERÖFFNUNG. Erleben Sie Wohnen im Industrial Design. Einfach und Modern - OHNE ZWISCHENHANDEL DIREKT ZU FABRIKPREISEN
andere Textvorschläge sind erwünscht

```html
<!DOCTYPE html>
<html lang="de">
<head>
<meta charset="utf-8">
<title>Neueröffnung – Massivholztische zu Fabrikpreisen</title>
<link href="https://fonts.googleapis.com/css2?family=Jost:wght@400&family=League+Spartan:wght@800&display=swap" rel="stylesheet">
<style>
  :root {
    --wall-light: #d3cdc2;
    --wall-mid: #a59d90;
    --wall-dark: #6f695f;
    --wood-light: #c9a37a;
    --leather: #8a4a26;
    --floor-warm: #7d5b40;
    --floor-dark: #4a3626;
    --steel: #2a2623;
    --panel-blue: rgba(28, 104, 176, 0.86);
    --accent-orange: #e0852a;
    --text-white: #ffffff;
  }
  html, body {
    margin: 0;
    padding: 0;
    width: 1200px;
    height: 611px;
    overflow: hidden;
    background: #ffffff;
  }
  .poster {
    display: block;
    width: 1200px;
    height: 611px;
  }
  .headline-light {
    font-family: "Jost", "Futura", sans-serif;
    font-weight: 400;
    fill: var(--text-white);
  }
  .headline-heavy {
    font-family: "League Spartan", "Futura", sans-serif;
    font-weight: 800;
    fill: var(--accent-orange);
  }
  .rule {
    stroke: var(--text-white);
    stroke-width: 2.5;
  }
</style>
</head>
<body>
<svg class="poster" viewBox="0 0 1200 611" xmlns="http://www.w3.org/2000/svg">
  <defs>
    <linearGradient id="roomTones" x1="0" y1="0" x2="0" y2="1">
      <stop offset="0" stop-color="var(--wall-light)"/>
      <stop offset="0.3" stop-color="var(--wall-mid)"/>
      <stop offset="0.5" stop-color="var(--wall-dark)"/>
      <stop offset="0.6" stop-color="var(--floor-warm)"/>
      <stop offset="1" stop-color="var(--floor-dark)"/>
    </linearGradient>
    <linearGradient id="tableTones" x1="0" y1="0" x2="0" y2="1">
      <stop offset="0" stop-color="var(--wood-light)" stop-opacity="0"/>
      <stop offset="0.4" stop-color="var(--wood-light)" stop-opacity="0.75"/>
      <stop offset="1" stop-color="var(--wood-light)" stop-opacity="0"/>
    </linearGradient>
    <radialGradient id="leatherLeft" cx="0.2" cy="0.45" r="0.22">
      <stop offset="0" stop-color="var(--leather)" stop-opacity="0.7"/>
      <stop offset="1" stop-color="var(--leather)" stop-opacity="0"/>
    </radialGradient>
    <radialGradient id="leatherRight" cx="0.84" cy="0.42" r="0.18">
      <stop offset="0" stop-color="var(--leather)" stop-opacity="0.6"/>
      <stop offset="1" stop-color="var(--leather)" stop-opacity="0"/>
    </radialGradient>
    <radialGradient id="shadeLeft" cx="0.18" cy="0.82" r="0.25">
      <stop offset="0" stop-color="var(--steel)" stop-opacity="0.45"/>
      <stop offset="1" stop-color="var(--steel)" stop-opacity="0"/>
    </radialGradient>
  </defs>

  <g class="scene-photo" role="img" aria-label="Foto: Massivholztisch mit Stahlkufen, Lederstühle und Barhocker in einer alten Fabrikhalle mit Holzdielen">
    <rect x="0" y="0" width="1200" height="611" fill="url(#roomTones)"/>
    <rect x="0" y="90" width="1200" height="110" fill="url(#tableTones)"/>
    <rect x="0" y="0" width="1200" height="611" fill="url(#leatherLeft)"/>
    <rect x="0" y="0" width="1200" height="611" fill="url(#leatherRight)"/>
    <rect x="0" y="0" width="1200" height="611" fill="url(#shadeLeft)"/>
  </g>

  <rect class="title-panel" x="339" y="0" width="509" height="611" fill="var(--panel-blue)"/>

  <line class="rule" x1="389" y1="37" x2="812" y2="37"/>

  <text class="headline-light" x="388" y="97" font-size="54" textLength="425" lengthAdjust="spacingAndGlyphs">NEUERÖFFNUNG</text>

  <text class="headline-heavy" x="356" y="216" font-size="134" textLength="470" lengthAdjust="spacingAndGlyphs">MASSIV</text>
  <text class="headline-heavy" x="344" y="356" font-size="198" textLength="498" lengthAdjust="spacingAndGlyphs">HOLZ</text>
  <text class="headline-heavy" x="356" y="452" font-size="138" textLength="464" lengthAdjust="spacingAndGlyphs">TISCHE</text>

  <text class="headline-light" x="386" y="522" font-size="50" textLength="427" lengthAdjust="spacingAndGlyphs">ZU FABRIKPREISEN</text>

  <line class="rule" x1="389" y1="545" x2="812" y2="545"/>
</svg>
</body>
</html>
```